Simple and clean

We need a business card design for a new company called Dwelling Hawk. It is a search engine to find current properties for sale or rent in New Zealand market.
We have already a colour scheme that we would like people to use.
Light brown: #D4CCB0
Light green: #D6E4D4
Green: #669966
Black/White
It is OK to divert from this colour scheme slightly as long as there is a green component to the business card.
Final design should be clean, simple and should communicate the nature of the business.
Target Market(s)
- First home buyers
- Real estate agents
- People seeking rentals
Industry/Entity Type
Business
Requirements
Must have
- Use those or similar colours.
Light brown: #D4CCB0
Light green: #D6E4D4
Green: #669966
Black/White

```html
<!DOCTYPE html>
<html lang="en">
<head>
<meta charset="utf-8">
<title>Dwelling Hawk – Business Card</title>
<link rel="stylesheet" href="https://fonts.googleapis.com/css2?family=Arimo:wght@700&display=swap">
<style>
  :root {
    --white: #ffffff;
    --black: #000000;
    --light-green: #d6e4d4;
    --light-brown: #d4ccb0;
    --green: #669966;
    --bracket-green: #6d9a6a;
    --ink: #111111;
  }
  * { box-sizing: border-box; margin: 0; padding: 0; }
  html, body {
    width: 1200px;
    height: 700px;
    overflow: hidden;
    background: var(--white);
  }
  .card {
    position: relative;
    width: 1200px;
    height: 700px;
    overflow: hidden;
    background: var(--white);
    font-family: "Arimo", Arial, sans-serif;
    font-weight: 700;
    color: var(--ink);
  }
  .header-band {
    position: absolute;
    left: 0; top: 142px;
    width: 1200px; height: 91px;
    background: var(--light-green);
  }
  .brand-disc {
    position: absolute;
    left: 29px; top: 52px;
    width: 164px; height: 164px;
    border-radius: 50%;
    background: var(--white);
  }
  .brand-name {
    position: absolute;
    left: 213px; top: 80px;
    font-size: 58px;
    line-height: 1;
    letter-spacing: -1px;
    color: var(--ink);
  }
  .values-panel {
    position: absolute;
    left: 0; top: 233px;
    width: 580px; height: 342px;
    background: var(--light-brown);
  }
  .values-list {
    list-style: none;
    position: absolute;
    left: 70px; top: 48px;
  }
  .value {
    display: flex;
    align-items: center;
    height: 50px;
    margin-bottom: 51px;
    font-size: 37px;
    color: var(--ink);
  }
  .initial {
    position: relative;
    display: inline-block;
    width: 46px;
    height: 48px;
    line-height: 48px;
    text-align: center;
    margin-right: 2px;
  }
  .initial::before,
  .initial::after {
    content: "";
    position: absolute;
    top: 0;
    width: 7px;
    height: 46px;
    border: 2px solid var(--bracket-green);
  }
  .initial::before { left: 0; border-right: none; }
  .initial::after { right: 0; border-left: none; }
  .contact-panel {
    position: absolute;
    left: 580px; top: 233px;
    width: 620px; height: 342px;
    background: var(--green);
    text-align: center;
    color: var(--ink);
  }
  .person-name {
    position: absolute;
    left: 0; right: 0; top: 100px;
    font-size: 29px;
  }
  .person-role {
    position: absolute;
    left: 0; right: 0; top: 136px;
    font-size: 20px;
  }
  .contact-line {
    position: absolute;
    left: 0; right: 0;
    font-size: 21px;
  }
  .contact-mobile { top: 268px; }
  .contact-email { top: 304px; }
  .web-band {
    position: absolute;
    left: 0; top: 575px;
    width: 1200px; height: 125px;
    background: var(--black);
    display: flex;
    align-items: center;
    justify-content: center;
  }
  .web-address {
    color: var(--white);
    font-size: 50px;
    letter-spacing: 15px;
    margin-right: -15px;
  }
</style>
</head>
<body>
  <div class="card">
    <div class="header-band"></div>
    <div class="brand-disc"></div>
    <div class="brand-name">Dwelling Hawk</div>

    <section class="values-panel">
      <ul class="values-list">
        <li class="value"><span class="initial">L</span>ocate</li>
        <li class="value"><span class="initial">E</span>valuate</li>
        <li class="value"><span class="initial">A</span>ccommodate</li>
      </ul>
    </section>

    <section class="contact-panel">
      <p class="person-name">Marcel Dupree</p>
      <p class="person-role">Director</p>
      <p class="contact-line contact-mobile">Mobile: 0427 518 206</p>
      <p class="contact-line contact-email">Email: marceldupree@dwellinghawk.co.nz</p>
    </section>

    <footer class="web-band">
      <p class="web-address">www.dwellinghawk.co.nz</p>
    </footer>
  </div>
</body>
</html>
```